Business Card Design for Flood Rescue 360 - Property Restoration Professionals

I need a business card designed for Flood Rescue 360. We are a full-service property restoration solution. Providing water, fire, smoke & storm restoration as well as mold remediation and full remodel or reconstruction to homes and businesses across Dallas-Fort Worth, TX.
Target Market(s)
home and business owners with insurance covered property damage from water, fire or storm related damage
Industry/Entity Type
property restoration
Contact Information for Business Card
Marcus Pelley General Manager Cell: 214-555-0193 Office: 469-555-0148 email: Marcus@FloodRescue360.example services: Water, Fire, Mold, Reconstruction Tagline: Urgency for Your Water Emergency!
Look and feel
Each slider illustrates characteristics of the customer's brand and the style your logo design should communicate.

```html
<!DOCTYPE html>
<html lang="en">
<head>
<meta charset="utf-8">
<title>Flood Rescue 360 – Business Card</title>
<link rel="stylesheet" href="https://fonts.googleapis.com/css2?family=Roboto:wght@400;500;700;900&display=swap">
<style>
  :root {
    --stage: #111111;
    --front-bg: #797b7a;
    --front-ink: #5e6160;
    --front-light: #f4f4f4;
    --paper: #ffffff;
    --brand-blue: #1ab3e6;
    --brand-grey: #767676;
    --ink: #1d1d1d;
    --tint-blue: #e3f2fb;
    --tint-grey: #e9e9ea;
  }
  * { box-sizing: border-box; margin: 0; padding: 0; }
  html, body { width: 1200px; height: 960px; overflow: hidden; }
  body {
    background: var(--stage);
    font-family: "Roboto", Arial, sans-serif;
    position: relative;
  }
  .card {
    position: absolute;
    left: 249px;
    width: 702px;
    height: 401px;
    overflow: hidden;
    box-shadow: 0 10px 24px rgba(0,0,0,0.6);
  }

  /* Front */
  .card-front { top: 60px; background: var(--front-bg); }
  .front-brand {
    position: absolute;
    left: 0; right: 0; top: 132px;
    display: flex; align-items: center; justify-content: center; gap: 22px;
  }
  .front-brand .brand-name {
    color: var(--front-ink);
    font-weight: 900;
    font-size: 56px;
    line-height: 0.98;
    text-transform: uppercase;
    text-align: right;
    letter-spacing: -1px;
  }
  .front-brand .brand-dot {
    width: 124px; height: 124px; border-radius: 50%;
    border: 10px solid var(--front-light);
  }
  .services {
    position: absolute; left: 0; right: 0; top: 335px;
    color: var(--front-light); text-align: center;
  }
  .services-heading {
    display: flex; align-items: center; justify-content: center; gap: 8px;
    font-size: 17px; letter-spacing: 0.5px;
  }
  .services-heading .rule {
    width: 122px; height: 2px;
    background: linear-gradient(90deg, transparent, var(--front-light));
  }
  .services-heading .rule.right {
    background: linear-gradient(90deg, var(--front-light), transparent);
  }
  .services-list {
    margin-top: 4px;
    display: flex; justify-content: center; gap: 8px;
    font-size: 17px; letter-spacing: 0.6px;
  }
  .services-list li { list-style: none; display: flex; align-items: center; gap: 5px; }
  .services-list li::before {
    content: ""; width: 10px; height: 10px; border-radius: 50%;
    border: 1.5px solid var(--front-light);
  }

  /* Back */
  .card-back { top: 500px; background: var(--paper); }
  .back-decor {
    position: absolute; left: -30px; top: 0; width: 380px; height: 401px;
  }
  .back-brand {
    position: absolute; right: 29px; top: 22px;
    display: flex; align-items: center; gap: 14px;
  }
  .back-brand .brand-name {
    color: var(--brand-blue);
    font-weight: 900;
    font-size: 50px;
    line-height: 0.98;
    text-transform: uppercase;
    text-align: right;
    letter-spacing: -1px;
  }
  .back-brand .brand-dot {
    width: 96px; height: 96px; border-radius: 50%;
    border: 8px solid var(--brand-blue);
  }
  .accent-bar {
    position: absolute; right: 0; top: 172px;
    width: 21px; height: 56px; background: var(--brand-blue);
  }
  .person { position: absolute; right: 29px; top: 168px; text-align: right; }
  .person-name { font-size: 36px; line-height: 1.1; color: var(--brand-grey); font-weight: 400; }
  .person-name .first { color: var(--brand-blue); font-weight: 500; }
  .person-title { font-size: 18px; color: var(--ink); letter-spacing: 0.3px; }
  .tagline {
    position: absolute; right: 29px; top: 258px;
    color: var(--brand-blue); font-size: 17.5px; letter-spacing: 0.3px;
  }
  .contacts { position: absolute; right: 29px; top: 302px; list-style: none; }
  .contacts li {
    display: flex; justify-content: flex-end; align-items: center; gap: 12px;
    font-size: 17.5px; color: var(--ink); letter-spacing: 0.6px; height: 23.5px;
  }
  .contacts svg { width: 15px; height: 15px; flex: none; }
</style>
</head>
<body>

<section class="card card-front" aria-label="Card front">
  <div class="front-brand">
    <div class="brand-name">Flood<br>Rescue 360</div>
    <div class="brand-dot" aria-hidden="true"></div>
  </div>
  <div class="services">
    <div class="services-heading"><span class="rule"></span>SERVICES<span class="rule right"></span></div>
    <ul class="services-list">
      <li>Water</li><li>Fire</li><li>Mold</li><li>Reconstruction</li>
    </ul>
  </div>
</section>

<section class="card card-back" aria-label="Card back">
  <svg class="back-decor" viewBox="0 0 380 401" aria-hidden="true">
    <circle cx="175" cy="210" r="190" fill="none" stroke="var(--tint-blue)" stroke-width="34"/>
    <path d="M35 320 A190 190 0 0 0 330 330" fill="none" stroke="var(--tint-grey)" stroke-width="34"/>
  </svg>

  <div class="back-brand">
    <div class="brand-name">Flood<br>Rescue 360</div>
    <div class="brand-dot" aria-hidden="true"></div>
  </div>

  <div class="accent-bar" aria-hidden="true"></div>
  <div class="person">
    <div class="person-name"><span class="first">Marcus</span> Pelley</div>
    <div class="person-title">General Manager</div>
  </div>

  <p class="tagline">Urgency for Your Water Emergency!</p>

  <ul class="contacts">
    <li>214-555-0193
      <svg viewBox="0 0 16 16" aria-label="Cell"><rect x="4" y="1" width="8" height="14" rx="1.5" fill="none" stroke="var(--brand-blue)" stroke-width="1.5"/><line x1="7" y1="12.5" x2="9" y2="12.5" stroke="var(--brand-blue)" stroke-width="1.2"/></svg>
    </li>
    <li>469-555-0148
      <svg viewBox="0 0 16 16" aria-label="Office"><path d="M3 2 L6 2 L7 5 L5.5 6.5 Q7 9.5 9.5 10.5 L11 9 L14 10 L14 13 Q13 14.5 11 14 Q4 12 2 5 Q1.5 3 3 2 Z" fill="none" stroke="var(--brand-blue)" stroke-width="1.4"/></svg>
    </li>
    <li>Marcus@FloodRescue360.example
      <svg viewBox="0 0 16 16" aria-label="Email"><rect x="1" y="4" width="14" height="10" rx="1" fill="var(--brand-blue)"/><path d="M1 4 L8 10 L15 4" fill="none" stroke="#fff" stroke-width="1.2"/></svg>
    </li>
  </ul>
</section>

</body>
</html>
```